Create modern and sleek business card for luxury real estate company

We're a "boutique" real estate office looking for a design that gets across a highly modern luxury brand. Blacks and whites are probably the best colors unless we try a silver foil for the logo. I've attached a version of our current logo here. I'd like to swap out the current font on there with Gotham Light Regular.

I'm looking to have one side of the card have the logo with the space for our agents info on the other side.

Target Market(s)

Young professionals in a "luxury" headspace

Industry/Entity Type

Real estate

Contact Information for Business Card

A place for agent name, cell number, website. The slogan "Quietly Redefining Fine Homes".

Font styles to use
Other font styles liked:
• Gotham Regular

Colors

Designer to choose only greyscale colors for use in the design.

Requirements
Must have
• Matte black as the background color. Clean lines and use of contrast. A specific design aspect that will use silver foil.
Nice to have
• Up in the air on integrating a QR code
Should not have
• Any houses or other real estate related design (ex: a clip art house)

```html
<!DOCTYPE html>
<html lang="en">
<head>
<meta charset="utf-8">
<title>Vantage Realty – Business Card</title>
<link rel="stylesheet" href="https://fonts.googleapis.com/css2?family=Open+Sans:wght@300;400;700&display=swap">
<style>
  :root {
    --backdrop: #3b3b3d;
    --card-black: #0d0d0d;
    --silver: #e9e9e9;
    --grey-text: #8a8a8a;
    --rule: #6f6f6f;
    --pattern-dark: #141414;
    --pattern-light: #2a2a2a;
  }
  * { box-sizing: border-box; margin: 0; padding: 0; }
  html, body {
    width: 1200px; height: 801px; overflow: hidden;
    background: var(--backdrop);
    font-family: "Open Sans", Arial, sans-serif;
  }
  .stage {
    position: relative; width: 1200px; height: 801px;
    display: flex; align-items: center; justify-content: center; gap: 50px;
  }
  .card {
    position: relative; width: 525px; height: 300px;
    background: var(--card-black);
    border-radius: 3px;
    box-shadow: 0 14px 30px rgba(0,0,0,.45);
    overflow: hidden;
  }
  /* front: agent side */
  .brand {
    position: absolute; left: 34px; top: 108px;
    display: flex; align-items: center; gap: 14px;
  }
  .brand-circle {
    width: 58px; height: 58px; border-radius: 50%;
    border: 2px solid var(--silver); flex: none;
  }
  .brand-name {
    color: var(--silver); font-weight: 400; font-size: 25px;
    line-height: 1.05; letter-spacing: 1px; text-transform: uppercase;
    white-space: nowrap;
  }
  .divider {
    position: absolute; left: 272px; top: 70px;
    width: 1px; height: 118px; background: var(--rule);
  }
  .agent { position: absolute; left: 292px; top: 70px; }
  .agent-name {
    color: var(--silver); font-weight: 700; font-size: 17px;
    letter-spacing: .5px; text-transform: uppercase; white-space: nowrap;
  }
  .agent-title { color: var(--grey-text); font-size: 13px; margin: 2px 0 12px; }
  .contact-list { list-style: none; }
  .contact-list li {
    display: flex; align-items: center; gap: 8px; white-space: nowrap;
    color: var(--silver); font-size: 13px; font-weight: 300; line-height: 22px;
  }
  .contact-list svg { width: 10px; height: 10px; fill: var(--silver); flex: none; }
  .slogan {
    position: absolute; left: 292px; bottom: 52px;
    color: var(--silver); font-size: 13px; font-weight: 300; white-space: nowrap;
  }
  /* back: logo side */
  .pattern-field {
    position: absolute; inset: 0;
    background: linear-gradient(120deg, var(--pattern-dark) 0%, var(--pattern-light) 55%, var(--pattern-dark) 100%);
  }
  .back .brand { left: auto; right: 78px; top: auto; bottom: 86px; }
  .back .brand-circle { width: 50px; height: 50px; }
  .back .brand-name { font-size: 22px; }
</style>
</head>
<body>
<main class="stage">
  <section class="card front" aria-label="Agent side">
    <div class="brand">
      <div class="brand-circle"></div>
      <div class="brand-name">Vantage<br>Realty</div>
    </div>
    <div class="divider"></div>
    <div class="agent">
      <p class="agent-name">Daniel Harwood</p>
      <p class="agent-title">President</p>
      <ul class="contact-list">
        <li><svg viewBox="0 0 10 10"><path d="M2 0h2l1 3-1.4 1a5 5 0 0 0 2.4 2.4L7 5l3 1v2a2 2 0 0 1-2 2A8 8 0 0 1 0 2a2 2 0 0 1 2-2z"/></svg>555-014-2290</li>
        <li><svg viewBox="0 0 10 10"><path d="M0 2h10v6H0z M0 2l5 3.5L10 2" stroke="#0d0d0d" stroke-width=".8"/></svg>dharwood@vantagerealty.com</li>
        <li><svg viewBox="0 0 10 10"><circle cx="5" cy="5" r="5"/></svg>www.vantagerealty.com</li>
      </ul>
    </div>
    <p class="slogan">Quietly Redefining Fine Homes</p>
  </section>

  <section class="card back" aria-label="Logo side">
    <div class="pattern-field" role="img" aria-label="Tone-on-tone gloss pattern of repeated brand marks across the card"></div>
    <div class="brand">
      <div class="brand-circle"></div>
      <div class="brand-name">Vantage<br>Realty</div>
    </div>
  </section>
</main>
</body>
</html>
```